Mira Bloom Fitness Coaching Project

I am a personal trainer based in London. My services include one-on-one PT sessions, bootcamps.
I would like the design to be minimalistic. With light colours: white, pink, purple.
I specialise in weight loss, flexibility, mobility.

Tessa Brogan
Personal Trainer
Email: tessa.brogan@quellmail.com
tel: 07700218493
Instagram: Mira Bloom

Target Market(s)

adults, mostly females (age 18-50).

Industry/Entity Type

Fitness

Contact Information for Business Card

Tessa Brogan
Personal Trainer
tel: 07700218493
Instagram: Mira Bloom

Font styles to use
Serif

Colors
eea4c8
fbd4d5
fdf9cf
cfeae6
cee9f5

Requirements
Nice to have
• minimalistic style
• easy to read and remember

```html
<!DOCTYPE html>
<html lang="en">
<head>
<meta charset="utf-8">
<title>Tessa Brogan – Business Card</title>
<link rel="stylesheet" href="https://fonts.googleapis.com/css2?family=Tinos:wght@400&display=swap">
<style>
  :root {
    --backdrop: #f7f2f8;
    --card-stock: #fbe3ea;
    --card-edge: #efc9d6;
    --emboss-light: rgba(255, 255, 255, 0.95);
    --emboss-dark: rgba(158, 92, 130, 0.42);
    --ink-purple: #5b3a74;
  }
  html, body {
    margin: 0;
    padding: 0;
    width: 1200px;
    height: 800px;
    overflow: hidden;
    background: var(--backdrop);
  }
  .canvas {
    position: relative;
    width: 1200px;
    height: 800px;
  }
  .business-card {
    position: absolute;
    left: 145px;
    top: 140px;
    width: 910px;
    height: 520px;
    background: var(--card-stock);
    box-shadow: 0 0 0 1px var(--card-edge), 0 14px 34px rgba(120, 80, 120, 0.14);
    font-family: "Tinos", "Times New Roman", serif;
  }
  .embossed-name {
    position: absolute;
    right: 60px;
    top: 96px;
    margin: 0;
    font-size: 74px;
    font-weight: 400;
    line-height: 1;
    letter-spacing: 4px;
    white-space: nowrap;
    color: var(--card-stock);
    text-shadow:
      -1px -1px 1px var(--emboss-dark),
      1px 1px 1px var(--emboss-light),
      2px 2px 2px var(--emboss-light);
  }
  .contact-block {
    position: absolute;
    left: 360px;
    top: 300px;
    margin: 0;
    font-size: 23px;
    line-height: 1.18;
    letter-spacing: 1.2px;
    white-space: nowrap;
    color: var(--ink-purple);
    font-style: normal;
  }
  .contact-line {
    display: block;
  }
</style>
</head>
<body>
  <main class="canvas">
    <section class="business-card" aria-label="Business card">
      <h1 class="embossed-name">Tessa Brogan</h1>
      <address class="contact-block">
        <span class="contact-line">Tessa Brogan</span>
        <span class="contact-line">Personal Trainer</span>
        <span class="contact-line">Email: tessa.brogan@quellmail.com</span>
        <span class="contact-line">tel: 07700218493</span>
        <span class="contact-line">Instagram: Mira Bloom</span>
      </address>
    </section>
  </main>
</body>
</html>
```